Birchline Septic Solutions

Would like to see some single sided ones but would also like to see some double sided with one sided only being the logo. Owners name is Colin Vandro. Phone number is 555-214-0387
Services are pumping, inspections, installs, and repairs

Contact Information for Business Card

555-241-0387 Colin Vandro Maplecrest, OH

```html
<!DOCTYPE html>
<html lang="en">
<head>
<meta charset="utf-8">
<title>Birchline Septic Solutions – Business Cards</title>
<link rel="stylesheet" href="https://fonts.googleapis.com/css2?family=Archivo:wght@400;700;800&display=swap">
<style>
  :root {
    --backdrop: #3b3b3c;
    --card: #161616;
    --card-deep: #0d0d0d;
    --teal: #35c2b8;
    --white: #ffffff;
    --muted: #d6d6d6;
    --pattern-a: #1f1f1f;
    --pattern-b: #3a3a3a;
  }
  * { box-sizing: border-box; margin: 0; padding: 0; }
  html, body {
    width: 1200px; height: 801px; overflow: hidden;
    background: var(--backdrop);
    font-family: "Archivo", Arial, sans-serif;
  }
  .stage {
    position: relative; width: 1200px; height: 801px;
    display: flex; align-items: center; justify-content: center; gap: 60px;
  }
  .card {
    position: relative; width: 520px; height: 297px;
    background: var(--card);
    border-bottom: 3px solid var(--teal);
    border-left: 3px solid var(--teal);
    overflow: hidden;
  }

  /* Front */
  .owner {
    position: absolute; right: 36px; top: 28px; text-align: right;
  }
  .owner-name {
    font-size: 20px; font-weight: 700; color: var(--teal);
    text-transform: uppercase; letter-spacing: 0.5px; line-height: 1.2;
  }
  .owner-title { font-size: 13px; color: var(--muted); margin-top: 2px; }
  .brand {
    position: absolute; left: 40px; top: 96px;
    display: flex; flex-direction: column; gap: 8px;
  }
  .brand-name {
    display: flex; align-items: center; gap: 10px;
    font-size: 40px; font-weight: 800; color: var(--white);
    letter-spacing: 1px; line-height: 1;
  }
  .brand-mark { width: 15px; height: 15px; background: var(--teal); }
  .brand-tagline {
    font-size: 12px; font-weight: 400; color: var(--white);
    letter-spacing: 6px; text-transform: uppercase; padding-left: 2px;
  }
  .divider {
    position: absolute; left: 40px; right: 24px; top: 182px;
    height: 1px; background: var(--teal);
  }
  .contact-list {
    position: absolute; left: 40px; top: 194px;
    list-style: none; display: flex; flex-direction: column; gap: 4px;
  }
  .contact-item {
    display: flex; align-items: center; gap: 8px;
    font-size: 14px; line-height: 1.1; color: var(--muted);
  }
  .contact-icon { width: 11px; height: 11px; flex: none; fill: var(--teal); }

  /* Back */
  .card-back { background: var(--card-deep); }
  .back-pattern {
    position: absolute; inset: 0;
    background: linear-gradient(125deg, var(--pattern-a) 0%, var(--pattern-a) 35%, var(--pattern-b) 100%);
    opacity: 0.9;
  }
  .back-brand {
    position: absolute; left: 0; right: 0; top: 50%;
    transform: translateY(-50%);
    display: flex; align-items: center; justify-content: center; gap: 10px;
    font-size: 36px; font-weight: 800; color: var(--white);
    letter-spacing: 1px; line-height: 1;
  }
  .back-brand .brand-mark { width: 14px; height: 14px; }
</style>
</head>
<body>
<main class="stage">

  <section class="card card-front">
    <div class="owner">
      <div class="owner-name">Colin Vandro</div>
      <div class="owner-title">Founder / CEO</div>
    </div>

    <div class="brand">
      <div class="brand-name"><span>BIRCHLINE</span><span class="brand-mark"></span></div>
      <div class="brand-tagline">Septic Solutions</div>
    </div>

    <div class="divider"></div>

    <ul class="contact-list">
      <li class="contact-item">
        <svg class="contact-icon" viewBox="0 0 24 24"><path d="M6.6 10.8a15 15 0 0 0 6.6 6.6l2.2-2.2a1 1 0 0 1 1-.25 11.4 11.4 0 0 0 3.6.57 1 1 0 0 1 1 1V20a1 1 0 0 1-1 1A17 17 0 0 1 3 4a1 1 0 0 1 1-1h3.5a1 1 0 0 1 1 1c0 1.25.2 2.45.57 3.57a1 1 0 0 1-.25 1z"/></svg>
        555-241-0387
      </li>
      <li class="contact-item">
        <svg class="contact-icon" viewBox="0 0 24 24"><path d="M2 5h20v14H2z"/><path d="M3 6l9 7 9-7" fill="none" stroke="#161616" stroke-width="2"/></svg>
        info@birchlinesepticsolutions.com
      </li>
      <li class="contact-item">
        <svg class="contact-icon" viewBox="0 0 24 24"><circle cx="12" cy="12" r="10"/></svg>
        www.birchlinesepticsolutions.com
      </li>
      <li class="contact-item">
        <svg class="contact-icon" viewBox="0 0 24 24"><path d="M12 2a7 7 0 0 0-7 7c0 5.2 7 13 7 13s7-7.8 7-13a7 7 0 0 0-7-7zm0 9.5A2.5 2.5 0 1 1 12 6.5a2.5 2.5 0 0 1 0 5z"/></svg>
        Maplecrest, OH
      </li>
    </ul>
  </section>

  <section class="card card-back">
    <div class="back-pattern" role="img" aria-label="Tonal repeating brand pattern in glossy black on matte black"></div>
    <div class="back-brand"><span>BIRCHLINE</span><span class="brand-mark"></span></div>
  </section>

</main>
</body>
</html>
```